Tolvik Commercial Cleaning is lookong for a new business card design.

A fresh new design that's professional and stylish. We need a serious upgrade to our business cards. I have included pictures of our existing ones. Our clients include professional individuals and business owners. We woupdblike something professional and upbeat. Please have fun and see what you come uo with.

Target Market(s)

Property managers, business owners, facility managers and other similar professionals

Industry/Entity Type

Janitorial

Contact Information for Business Card

Name, cell, office number, email, web address

Font styles to use
Sans Serif

Colors

Designer to choose colors to be used in the design.

Requirements
Must have
• please use the green color in our logo
Nice to have
• Bar code
Should not have
• Address

```html
<!DOCTYPE html>
<html lang="en">
<head>
<meta charset="utf-8">
<title>Tolvik Commercial Cleaning – Business Card</title>
<link href="https://fonts.googleapis.com/css2?family=Montserrat:wght@400;500;600;700&display=swap" rel="stylesheet">
<style>
  :root {
    --brand-green: #43ae57;
    --deep-green: #2a9444;
    --ink: #333333;
    --muted: #444444;
    --card-white: #ffffff;
    --backdrop: #e8e5e0;
  }
  * { margin: 0; padding: 0; box-sizing: border-box; }
  html, body { width: 900px; height: 1200px; overflow: hidden; }
  body {
    background: var(--backdrop);
    font-family: "Montserrat", Arial, sans-serif;
    position: relative;
  }
  .card {
    position: absolute;
    left: 80px;
    width: 742px;
    height: 440px;
    border-radius: 40px;
  }
  .card-front { top: 132px; background: var(--card-white); }
  .card-back  { top: 638px; background: var(--brand-green); }

  .front-wordmark {
    position: absolute;
    left: 44px;
    top: 84px;
    color: var(--brand-green);
    font-weight: 700;
    line-height: 1;
  }
  .front-wordmark .wordmark-main { display: block; font-size: 96px; letter-spacing: -2px; }
  .front-wordmark .wordmark-sub  { display: block; font-size: 18px; margin-top: 6px; letter-spacing: 0.3px; }

  .holder {
    position: absolute;
    right: 36px;
    top: 208px;
    text-align: right;
  }
  .holder-name { color: var(--brand-green); font-weight: 700; font-size: 25px; }
  .holder-title { color: var(--muted); font-weight: 400; font-size: 15px; margin-top: 2px; }

  .divider {
    position: absolute;
    left: 46px;
    top: 247px;
    width: 524px;
    height: 1.5px;
    background: var(--brand-green);
  }

  .contact-list {
    position: absolute;
    left: 43px;
    top: 264px;
    list-style: none;
  }
  .contact-list li {
    display: flex;
    align-items: center;
    height: 22px;
    font-size: 16px;
    color: var(--ink);
  }
  .contact-list svg { width: 13px; height: 13px; margin-right: 12px; fill: var(--brand-green); }

  .back-wordmark {
    position: absolute;
    left: 0; right: 0;
    top: 108px;
    text-align: center;
    color: var(--deep-green);
    font-weight: 700;
    line-height: 1;
  }
  .back-wordmark .wordmark-main { display: block; font-size: 150px; letter-spacing: -4px; }
  .back-wordmark .wordmark-sub  { display: block; font-size: 30px; margin-top: 14px; }
</style>
</head>
<body>
  <section class="card card-front">
    <div class="front-wordmark">
      <span class="wordmark-main">Tolvik</span>
      <span class="wordmark-sub">Commercial Cleaning</span>
    </div>

    <div class="holder">
      <div class="holder-name">Marco Delgado</div>
      <div class="holder-title">CEO &amp; Founder</div>
    </div>

    <div class="divider"></div>

    <ul class="contact-list">
      <li>
        <svg viewBox="0 0 16 16" aria-hidden="true"><path d="M2 6c0-2 2-3 6-3s6 1 6 3v1h-3V5.5H5V7H2zM4 8h8l1 6H3z"/></svg>
        (37) 555-0182
      </li>
      <li>
        <svg viewBox="0 0 16 16" aria-hidden="true"><path d="M1 3h14v1.5L8 9 1 4.5zM1 6.3l7 4.5 7-4.5V13H1z"/></svg>
        marco@tolvikcleaning.com
      </li>
      <li>
        <svg viewBox="0 0 16 16" aria-hidden="true"><circle cx="8" cy="8" r="7"/><path d="M5 4l3 2-1 3-3-1zM10 9l2 1-2 3-1-2z" fill="#ffffff"/></svg>
        www.tolvikcleaning.com
      </li>
    </ul>
  </section>

  <section class="card card-back">
    <div class="back-wordmark">
      <span class="wordmark-main">Tolvik</span>
      <span class="wordmark-sub">Commercial Cleaning</span>
    </div>
  </section>
</body>
</html>
```